Travel Agency Website - Simple General

Need a 7 page simple design that is pretty repetitive. Need to be able to load quickly that is SEO optimized. Trying to give ideas on what they can do, be personal as we are local, but at the same time come across as professional and get information easily with little burden.

- Landing Page
- Brimwell Vacations Page
- Family Trips
- Road Trips from Texas
- Other Destinations
- About Us Page
- Contact Us Page

Target Market(s)

Families

Coding

Coded - Design and coding required

Number of Pages Required

5+ page

Colors

Designer to choose colors to be used in the design.

Requirements
Must have
• Like it to flow easily with our logo. Use that for colors, etc.

```html
<!DOCTYPE html>
<html lang="en">
<head>
<meta charset="utf-8">
<title>Meadowlark Journeys – Website Pages</title>
<link href="https://fonts.googleapis.com/css2?family=Poppins:wght@300;400;500;600;700;800&display=swap" rel="stylesheet">
<style>
:root{
  --bg:#d3d3d3;
  --cream:#fbf8f1;
  --mist:#e2ebe7;
  --teal:#3b7d7b;
  --ink:#15292e;
  --night:#122a2f;
  --gold:#b89a4f;
  --line:#e4ddd0;
  --text:#1d2b2e;
  --muted:#6b7476;
  --footer-text:#c9d3d1;
}
*{box-sizing:border-box;margin:0;padding:0}
html,body{width:1200px;height:2836px;overflow:hidden}
body{background:var(--bg);font-family:"Poppins",sans-serif;color:var(--text);position:relative}
ul{list-style:none}
em{font-style:normal}

.page{position:absolute;width:554px;display:flex;flex-direction:column;overflow:hidden;background:var(--cream);box-shadow:0 1px 4px rgba(0,0,0,.12)}
.nav{height:26px;flex:none;display:flex;align-items:center;justify-content:space-between;padding:0 40px;background:var(--cream);position:relative;z-index:2}
.brand{display:flex;align-items:center;gap:4px;font-size:6px;font-weight:600;color:var(--teal);white-space:nowrap}
.brand i{display:block;width:18px;height:18px;border-radius:50%;border:1px solid var(--teal);background:#fff}
.nav ul{display:flex;gap:9px;font-size:4.6px;text-transform:uppercase;color:var(--text);letter-spacing:.2px}
.nav li.active{color:var(--teal);border-bottom:.6px solid var(--teal)}

.hero{position:relative;flex:none;display:flex;flex-direction:column;align-items:center;justify-content:flex-end;color:#fff;text-align:center;padding-bottom:30px}
.hero-photo{position:absolute;inset:0}
.hero > *:not(.hero-photo){position:relative}
.tagline{font-size:13px;font-weight:400;letter-spacing:1.5px;text-transform:uppercase;line-height:1.2}
.hero h1{font-size:25px;font-weight:800;text-transform:uppercase;letter-spacing:.3px;line-height:1.15;margin-top:2px}
.hero p{font-size:4.8px;margin:4px 0 9px;opacity:.9}
.btn{display:inline-block;background:var(--gold);color:#fff;font-size:5.4px;text-transform:uppercase;padding:5px 9px;letter-spacing:.2px}
.btn.ghost{background:transparent;border:.8px solid #fff}
.btn-row{display:flex;gap:4px}

.content{position:relative;flex:1;background:linear-gradient(to bottom,var(--cream) 45%,var(--mist))}
.lead{position:absolute;font-size:17px;font-weight:800;text-transform:uppercase;line-height:1.5;color:var(--ink)}

.card{position:absolute;background:#fff;padding:6px 6px 8px;box-shadow:0 1px 4px rgba(0,0,0,.08)}
.card h2{background:var(--teal);color:#fff;font-weight:400;font-size:16px;text-align:center;text-transform:uppercase;padding:3px 0;margin-bottom:9px}
.fields{display:grid;grid-template-columns:1fr 1fr;gap:7px 10px}
.field.full{grid-column:1 / -1}
.field label{display:block;font-size:4.4px;font-weight:600;text-transform:uppercase;margin-bottom:2px}
.input{display:flex;justify-content:space-between;align-items:center;height:10px;border:.6px solid var(--line);background:var(--cream);font-size:3.6px;color:var(--muted);padding:0 3px}
.input.area{height:40px;align-items:flex-start;padding-top:3px}
.submit{display:block;margin-top:9px;background:var(--gold);color:#fff;text-align:center;font-size:5px;text-transform:uppercase;padding:5px 0}

.footer{height:128px;flex:none;background:var(--night);color:#e9eeec;padding:24px 40px 0;position:relative}
.footer .cols{display:grid;grid-template-columns:168px 95px 155px 1fr}
.footer .brand{color:#e9eeec;font-size:7px}
.footer .brand i{width:40px;height:40px;border-color:#e9eeec;background:transparent}
.footer .about{font-size:4.4px;line-height:1.55;margin-top:6px;width:120px;color:var(--footer-text)}
.footer h4{font-size:5px;font-weight:600;text-transform:uppercase;margin:12px 0 5px}
.footer li{font-size:4.4px;line-height:1.6;color:var(--footer-text)}
.footer .copy{position:absolute;left:0;right:0;bottom:7px;text-align:center;font-size:4.2px;color:var(--footer-text)}

.picks{position:absolute;left:41px;top:57px;display:flex;gap:5px}
.pick{position:relative;width:114px;height:177px}
.pick span{position:absolute;left:5px;bottom:4px;font-size:7px;color:#fff}
.pick b{position:absolute;right:4px;bottom:4px;width:9px;height:9px;background:var(--gold)}
.outline-btn{position:absolute;left:227px;top:264px;border:.8px solid var(--ink);font-size:5.4px;text-transform:uppercase;padding:5px 9px;color:var(--ink)}
.center-title{position:absolute;left:0;right:0;top:28px;text-align:center;font-size:17px;font-weight:800;text-transform:uppercase;color:var(--ink)}

.contact-block{position:absolute;left:41px;top:112px;width:185px;height:107px;display:flex}
.contact-block .shot{width:92px;height:100%}
.contact-block .info{flex:1;background:var(--teal);color:#fff;padding:10px 8px;font-size:4.4px;line-height:1.7}
.contact-block .info i{display:block;width:14px;height:14px;border-radius:50%;background:#fff;margin-bottom:8px}
.contact-block .info strong{display:block;font-size:5.4px;font-weight:600;text-transform:uppercase;margin-bottom:3px}

.about-photo{position:absolute;left:62px;top:28px;width:180px;height:175px}
.side-label{position:absolute;left:42px;top:200px;transform:rotate(-90deg);transform-origin:left top;font-size:5.4px;color:var(--gold);text-transform:uppercase;letter-spacing:.4px}
.side-rule{position:absolute;left:50px;top:28px;width:.8px;height:140px;background:var(--gold);opacity:.6}
.about-text{position:absolute;left:293px;top:56px;width:220px}
.about-text h3{font-size:17px;font-weight:800;text-transform:uppercase;color:var(--ink);margin-bottom:6px}
.about-text p{font-size:4.4px;line-height:1.6;margin-bottom:5px}
.about-text p.strong{font-weight:600}
</style>
</head>
<body>

<!-- Landing -->
<section class="page" style="left:31px;top:29px;height:720px">
  <header class="nav"><div class="brand"><i></i>Meadowlark Journeys</div>
    <ul><li class="active">Home</li><li>Brimwell Vacations</li><li>Family Trips</li><li>Texas Road Trips</li><li>Other Destinations</li><li>About Us</li><li>Contact Us</li></ul></header>
  <div class="hero" style="height:262px">
    <div class="hero-photo" role="img" aria-label="Two hikers in warm jackets overlooking misty autumn hills" style="background:linear-gradient(to bottom,#7d7b70,#5a5246 55%,#2f2822)"></div>
    <div class="tagline">Meadowlark Journeys</div>
    <h1>Adventure starts with one trip</h1>
    <p>Helping families create unforgettable Brimwell vacations, road trips, cruises, and custom travel experiences.</p>
    <div class="btn-row"><span class="btn">Start Planning</span><span class="btn ghost">Explore Destinations</span></div>
  </div>
  <div class="content">
    <div class="center-title">Choose your next adventure</div>
    <div class="picks">
      <div class="pick"><div role="img" aria-label="Green island over turquoise sea" style="position:absolute;inset:0;background:linear-gradient(#7fb3c8,#3f7f72 55%,#1f4e55)"></div><span>Brimwell Vacations</span><b></b></div>
      <div class="pick"><div role="img" aria-label="Family walking on a beach at sunset" style="position:absolute;inset:0;background:linear-gradient(#f1e3da,#d9b89c 55%,#6c5a4b)"></div><span>Family Trips</span><b></b></div>
      <div class="pick"><div role="img" aria-label="Two friends planning a trip with a globe" style="position:absolute;inset:0;background:linear-gradient(#c7c4bd,#8d7a66 55%,#2f3034)"></div><span>Texas Road Trips</span><b></b></div>
      <div class="pick"><div role="img" aria-label="Snowy mountain range under blue sky" style="position:absolute;inset:0;background:linear-gradient(#5e9ac4,#a6bccb 45%,#314a4c)"></div><span>Other Destinations</span><b></b></div>
    </div>
    <span class="outline-btn">Explore Destinations</span>
  </div>
  <footer class="footer">
    <div class="cols">
      <div><div class="brand"><i></i>Meadowlark Journeys</div><p class="about">From magical Brimwell vacations and relaxing cruises to unforgettable road trips and custom family adventures, we're here to turn your travel dreams into lasting memories.</p></div>
      <div><h4>Main Links</h4><ul><li>Brimwell Vacations</li><li>Family Trips</li><li>Texas Road Trips</li><li>Other Destinations</li><li>About Us</li><li>Contact Us</li></ul></div>
      <div><h4>Contact Us</h4><ul><li>☏ 00.00.000</li><li>✉ hello@meadowlarkjourneys.com</li></ul></div>
      <div><h4>Follow Us On</h4><ul><li>○ Pagebook</li><li>□ Snapgram</li></ul></div>
    </div>
    <div class="copy">© 2026 Meadowlark Journeys. All Rights Reserved.</div>
  </footer>
</section>

<!-- Other Destinations -->
<section class="page" style="left:615px;top:29px;height:656px">
  <header class="nav"><div class="brand"><i></i>Meadowlark Journeys</div>
    <ul><li>Home</li><li>Brimwell Vacations</li><li>Family Trips</li><li>Texas Road Trips</li><li class="active">Other Destinations</li><li>About Us</li><li>Contact Us</li></ul></header>
  <div class="hero" style="height:228px">
    <div class="hero-photo" role="img" aria-label="Snow-capped mountain range above a dark pine forest" style="background:linear-gradient(#5f95c0,#a7b7c0 40%,#3e5253 75%,#1a2a26)"></div>
    <div class="tagline">Meadowlark Journeys</div>
    <h1>Other Destinations</h1>
    <p>Discover custom travel experiences tailored to your dream destination and travel style.</p>
    <span class="btn">Plan Other Destination</span>
  </div>
  <div class="content">
    <div class="lead" style="left:42px;top:80px">Explore endless<br>travel possibilities</div>
    <div class="card" style="left:273px;top:35px;width:220px">
      <h2>Other Destinations</h2>
      <div class="fields">
        <div class="field"><label>Type of Trip</label><span class="input">Type of Trip <em>▾</em></span></div>
        <div class="field"><label>People</label><span class="input">1 <em>⇕</em></span></div>
        <div class="field"><label>Start Date</label><span class="input">dd-mm-yyyy <em>▦</em></span></div>
        <div class="field"><label>End Date</label><span class="input">dd-mm-yyyy <em>▦</em></span></div>
        <div class="field full"><label>Experience</label><span class="input">Kind of Trip <em>▾</em></span></div>
        <div class="field full"><label>Any Additional Notes</label><span class="input area">Type here...</span></div>
      </div>
      <span class="submit">Submit</span>
    </div>
  </div>
  <footer class="footer">
    <div class="cols">
      <div><div class="brand"><i></i>Meadowlark Journeys</div><p class="about">From magical Brimwell vacations and relaxing cruises to unforgettable road trips and custom family adventures, we're here to turn your travel dreams into lasting memories.</p></div>
      <div><h4>Main Links</h4><ul><li>Brimwell Vacations</li><li>Family Trips</li><li>Texas Road Trips</li><li>Other Destinations</li><li>About Us</li><li>Contact Us</li></ul></div>
      <div><h4>Contact Us</h4><ul><li>☏ 00.00.000</li><li>✉ hello@meadowlarkjourneys.com</li></ul></div>
      <div><h4>Follow Us On</h4><ul><li>○ Pagebook</li><li>□ Snapgram</li></ul></div>
    </div>
    <div class="copy">© 2026 Meadowlark Journeys. All Rights Reserved.</div>
  </footer>
</section>

<!-- Contact Us -->
<section class="page" style="left:615px;top:713px;height:656px">
  <header class="nav"><div class="brand"><i></i>Meadowlark Journeys</div>
    <ul><li>Home</li><li>Brimwell Vacations</li><li>Family Trips</li><li>Texas Road Trips</li><li>Other Destinations</li><li>About Us</li><li class="active">Contact Us</li></ul></header>
  <div class="hero" style="height:228px">
    <div class="hero-photo" role="img" aria-label="Two hikers pointing toward distant hills" style="background:linear-gradient(to bottom,#7d7b70,#5a5246 55%,#2f2822)"></div>
    <div class="tagline">Meadowlark Journeys</div>
    <h1>Contact Us</h1>
    <p>Share your travel ideas, questions, or dream destinations, and we'll help you plan a stress-free adventure tailored to your family.</p>
    <span class="btn">Plan Other Destination</span>
  </div>
  <div class="content">
    <div class="lead" style="left:42px;top:52px">Let's create your<br>perfect vacation</div>
    <div class="contact-block">
      <div class="shot" role="img" aria-label="Laptop showing a travel booking page" style="background:linear-gradient(#dfe7ee,#9fb6c6 60%,#5f7480)"></div>
      <div class="info"><i></i><strong>Contact Us</strong>☏ 00.00.000<br>✉ hello@meadowlark<br>journeys.com</div>
    </div>
    <div class="card" style="left:269px;top:30px;width:229px">
      <h2>Get in Touch</h2>
      <div class="fields">
        <div class="field"><label>First Name</label><span class="input">Write Here...</span></div>
        <div class="field"><label>Last Name</label><span class="input">Write Here...</span></div>
        <div class="field"><label>Email</label><span class="input">Write Here...</span></div>
        <div class="field"><label>Phone No.</label><span class="input">Write Here... <em>⇕</em></span></div>
        <div class="field full"><label>Any Additional Notes</label><span class="input area">Write Here...</span></div>
      </div>
      <span class="submit">Submit</span>
    </div>
  </div>
  <footer class="footer">
    <div class="cols">
      <div><div class="brand"><i></i>Meadowlark Journeys</div><p class="about">From magical Brimwell vacations and relaxing cruises to unforgettable road trips and custom family adventures, we're here to turn your travel dreams into lasting memories.</p></div>
      <div><h4>Main Links</h4><ul><li>Brimwell Vacations</li><li>Family Trips</li><li>Texas Road Trips</li><li>Other Destinations</li><li>About Us</li><li>Contact Us</li></ul></div>
      <div><h4>Contact Us</h4><ul><li>☏ 00.00.000</li><li>✉ hello@meadowlarkjourneys.com</li></ul></div>
      <div><h4>Follow Us On</h4><ul><li>○ Pagebook</li><li>□ Snapgram</li></ul></div>
    </div>
    <div class="copy">© 2026 Meadowlark Journeys. All Rights Reserved.</div>
  </footer>
</section>

<!-- Brimwell Vacations -->
<section class="page" style="left:31px;top:778px;height:656px">
  <header class="nav"><div class="brand"><i></i>Meadowlark Journeys</div>
    <ul><li>Home</li><li class="active">Brimwell Vacations</li><li>Family Trips</li><li>Texas Road Trips</li><li>Other Destinations</li><li>About Us</li><li>Contact Us</li></ul></header>
  <div class="hero" style="height:228px">
    <div class="hero-photo" role="img" aria-label="Forested island rising from a teal sea" style="background:linear-gradient(#a9c2c7,#5d8a8a 40%,#2f6b6f 70%,#1c3a3a)"></div>
    <div class="tagline">Meadowlark Journeys</div>
    <h1>Brimwell Vacations</h1>
    <p>Magical Brimwell park vacations and unforgettable cruise experiences designed for the whole family.</p>
    <span class="btn">Plan Your Brimwell Trip</span>
  </div>
  <div class="content">
    <div class="card" style="left:41px;top:32px;width:230px">
      <h2>Brimwell World</h2>
      <div class="fields">
        <div class="field"><label>People</label><span class="input">1 <em>⇕</em></span></div>
        <div class="field"><label>Start Date</label><span class="input">dd-mm-yyyy <em>▦</em></span></div>
        <div class="field"><label>End Date</label><span class="input">dd-mm-yyyy <em>▦</em></span></div>
        <div class="field"><label>Parks</label><span class="input">1 <em>⇕</em></span></div>
        <div class="field"><label>Resorts</label><span class="input">Preferred Resort <em>▾</em></span></div>
        <div class="field"><label>Experience</label><span class="input">Kind of Trip <em>▾</em></span></div>
        <div class="field full"><label>Any Additional Notes</label><span class="input area">Type here...</span></div>
      </div>
      <span class="submit">Submit</span>
    </div>
    <div class="card" style="left:282px;top:32px;width:230px">
      <h2>Brimwell Cruise</h2>
      <div class="fields">
        <div class="field"><label>People</label><span class="input">1 <em>⇕</em></span></div>
        <div class="field"><label>Months</label><span class="input">mm <em>▦</em></span></div>
        <div class="field"><label>Night Cruise</label><span class="input">1 <em>⇕</em></span></div>
        <div class="field"><label>Specific Cruise</label><span class="input">1 <em>⇕</em></span></div>
        <div class="field full"><label>Experience</label><span class="input">Kind of Trip <em>▾</em></span></div>
        <div class="field full"><label>Any Additional Notes</label><span class="input area">Type here...</span></div>
      </div>
      <span class="submit">Submit</span>
    </div>
  </div>
  <footer class="footer">
    <div class="cols">
      <div><div class="brand"><i></i>Meadowlark Journeys</div><p class="about">From magical Brimwell vacations and relaxing cruises to unforgettable road trips and custom family adventures, we're here to turn your travel dreams into lasting memories.</p></div>
      <div><h4>Main Links</h4><ul><li>Brimwell Vacations</li><li>Family Trips</li><li>Texas Road Trips</li><li>Other Destinations</li><li>About Us</li><li>Contact Us</li></ul></div>
      <div><h4>Contact Us</h4><ul><li>☏ 00.00.000</li><li>✉ hello@meadowlarkjourneys.com</li></ul></div>
      <div><h4>Follow Us On</h4><ul><li>○ Pagebook</li><li>□ Snapgram</li></ul></div>
    </div>
    <div class="copy">© 2026 Meadowlark Journeys. All Rights Reserved.</div>
  </footer>
</section>

<!-- About Us -->
<section class="page" style="left:615px;top:1400px;height:615px">
  <header class="nav"><div class="brand"><i></i>Meadowlark Journeys</div>
    <ul><li>Home</li><li>Brimwell Vacations</li><li>Family Trips</li><li>Texas Road Trips</li><li>Other Destinations</li><li class="active">About Us</li><li>Contact Us</li></ul></header>
  <div class="hero" style="height:228px">
    <div class="hero-photo" role="img" aria-label="Wooden pier leading to a green tropical island under blue sky" style="background:linear-gradient(#4f84bf,#a6c0d6 40%,#3f7a6a 65%,#1f4a4c)"></div>
    <div class="tagline">Meadowlark Journeys</div>
    <h1>About Us</h1>
    <p>Learn more about our family, our passion for travel, and how we help create unforgettable adventures for families like yours.</p>
    <span class="btn">Learn More</span>
  </div>
  <div class="content">
    <div class="side-rule"></div>
    <div class="side-label">About Us</div>
    <div class="about-photo" role="img" aria-label="Smiling family playing with a toy airplane outdoors" style="background:linear-gradient(#a8b58e,#7b5b4a 55%,#8f2f34)"></div>
    <div class="about-text">
      <h3>Our Family</h3>
      <p>We're a family that believes the best memories are made through travel, adventure, and quality time together. From magical Brimwell vacations and relaxing cruises to exciting road trips and custom getaways, we love exploring new places and helping other families do the same.</p>
      <p>What started as a passion for planning our own adventures quickly turned into helping friends and families create stress-free vacations filled with unforgettable experiences. We understand how important family time is, which is why we focus on making travel simple, personalized, and enjoyable for every family we work with.</p>
      <p class="strong">Our goal is to help you spend less time worrying about planning and more time making memories that will last a lifetime.</p>
    </div>
  </div>
  <footer class="footer">
    <div class="cols">
      <div><div class="brand"><i></i>Meadowlark Journeys</div><p class="about">From magical Brimwell vacations and relaxing cruises to unforgettable road trips and custom family adventures, we're here to turn your travel dreams into lasting memories.</p></div>
      <div><h4>Main Links</h4><ul><li>Brimwell Vacations</li><li>Family Trips</li><li>Texas Road Trips</li><li>Other Destinations</li><li>About Us</li><li>Contact Us</li></ul></div>
      <div><h4>Contact Us</h4><ul><li>☏ 00.00.000</li><li>✉ hello@meadowlarkjourneys.com</li></ul></div>
      <div><h4>Follow Us On</h4><ul><li>○ Pagebook</li><li>□ Snapgram</li></ul></div>
    </div>
    <div class="copy">© 2026 Meadowlark Journeys. All Rights Reserved.</div>
  </footer>
</section>

<!-- Family Trips -->
<section class="page" style="left:31px;top:1466px;height:656px">
  <header class="nav"><div class="brand"><i></i>Meadowlark Journeys</div>
    <ul><li>Home</li><li>Brimwell Vacations</li><li class="active">Family Trips</li><li>Texas Road Trips</li><li>Other Destinations</li><li>About Us</li><li>Contact Us</li></ul></header>
  <div class="hero" style="height:228px">
    <div class="hero-photo" role="img" aria-label="Parents and child playing on a beach beside a car at sunset" style="background:linear-gradient(#d8cfc2,#9c8d7a 50%,#3b3430)"></div>
    <div class="tagline">Meadowlark Journeys</div>
    <h1>Family Trips</h1>
    <p>Family adventures designed for fun, connection, and lasting memories.</p>
    <span class="btn">Plan Your Family Trip</span>
  </div>
  <div class="content">
    <div class="lead" style="left:42px;top:80px">Plan your perfect<br>family getaway</div>
    <div class="card" style="left:273px;top:32px;width:220px">
      <h2>Family Trips</h2>
      <div class="fields">
        <div class="field"><label>Destination</label><span class="input">Destination <em>▾</em></span></div>
        <div class="field"><label>People</label><span class="input">1 <em>⇕</em></span></div>
        <div class="field"><label>Start Date</label><span class="input">dd-mm-yyyy <em>▦</em></span></div>
        <div class="field"><label>End Date</label><span class="input">dd-mm-yyyy <em>▦</em></span></div>
        <div class="field full"><label>Experience</label><span class="input">Kind of Trip <em>▾</em></span></div>
        <div class="field full"><label>Any Additional Notes</label><span class="input area">Type here...</span></div>
      </div>
      <span class="submit">Submit</span>
    </div>
  </div>
  <footer class="footer">
    <div class="cols">
      <div><div class="brand"><i></i>Meadowlark Journeys</div><p class="about">From magical Brimwell vacations and relaxing cruises to unforgettable road trips and custom family adventures, we're here to turn your travel dreams into lasting memories.</p></div>
      <div><h4>Main Links</h4><ul><li>Brimwell Vacations</li><li>Family Trips</li><li>Texas Road Trips</li><li>Other Destinations</li><li>About Us</li><li>Contact Us</li></ul></div>
      <div><h4>Contact Us</h4><ul><li>☏ 00.00.000</li><li>✉ hello@meadowlarkjourneys.com</li></ul></div>
      <div><h4>Follow Us On</h4><ul><li>○ Pagebook</li><li>□ Snapgram</li></ul></div>
    </div>
    <div class="copy">© 2026 Meadowlark Journeys. All Rights Reserved.</div>
  </footer>
</section>

<!-- Texas Road Trips -->
<section class="page" style="left:31px;top:2151px;height:656px">
  <header class="nav"><div class="brand"><i></i>Meadowlark Journeys</div>
    <ul><li>Home</li><li>Brimwell Vacations</li><li>Family Trips</li><li class="active">Texas Road Trips</li><li>Other Destinations</li><li>About Us</li><li>Contact Us</li></ul></header>
  <div class="hero" style="height:228px">
    <div class="hero-photo" role="img" aria-label="Three friends planning a road trip around a globe" style="background:linear-gradient(#a9a39a,#6f5c4c 50%,#2a2522)"></div>
    <div class="tagline">Meadowlark Journeys</div>
    <h1>Road Trips from Texas</h1>
    <p>Explore scenic Texas road trips with flexible travel plans, family-friendly adventures, and optional van rentals for the perfect getaway.</p>
    <span class="btn">Plan Your Road Trip</span>
  </div>
  <div class="content">
    <div class="lead" style="left:42px;top:80px">Start your Texas<br>road trip adventure</div>
    <div class="card" style="left:273px;top:32px;width:220px">
      <h2>Road Trips</h2>
      <div class="fields">
        <div class="field"><label>Destination</label><span class="input">Destination <em>▾</em></span></div>
        <div class="field"><label>People</label><span class="input">1 <em>⇕</em></span></div>
        <div class="field"><label>Start Date</label><span class="input">dd-mm-yyyy <em>▦</em></span></div>
        <div class="field"><label>End Date</label><span class="input">dd-mm-yyyy <em>▦</em></span></div>
        <div class="field full"><label>Van Rental</label><span class="input">Type of van <em>▾</em></span></div>
        <div class="field full"><label>Any Additional Notes</label><span class="input area">Type here...</span></div>
      </div>
      <span class="submit">Submit</span>
    </div>
  </div>
  <footer class="footer">
    <div class="cols">
      <div><div class="brand"><i></i>Meadowlark Journeys</div><p class="about">From magical Brimwell vacations and relaxing cruises to unforgettable road trips and custom family adventures, we're here to turn your travel dreams into lasting memories.</p></div>
      <div><h4>Main Links</h4><ul><li>Brimwell Vacations</li><li>Family Trips</li><li>Texas Road Trips</li><li>Other Destinations</li><li>About Us</li><li>Contact Us</li></ul></div>
      <div><h4>Contact Us</h4><ul><li>☏ 00.00.000</li><li>✉ hello@meadowlarkjourneys.com</li></ul></div>
      <div><h4>Follow Us On</h4><ul><li>○ Pagebook</li><li>□ Snapgram</li></ul></div>
    </div>
    <div class="copy">© 2026 Meadowlark Journeys. All Rights Reserved.</div>
  </footer>
</section>

</body>
</html>
```